Business Card Design for Training Business

Clear Path Coaching is a new business that delivers training and other services with a focus on topics related to mental health and wellbeing, for example, Wellmind Response Course, Resilience etc. We have a strong focus on evidence-based psychology and neuroscience. I have a logo which I will upload with the brief, so please consider colours that work well with the logo.
Target Market(s)
Adults, workplaces (particularly government and not-for-profits)
Industry/Entity Type
Business
Contact Information for Business Card
Head Strong TrainingSamantha SellwoodDirector0438 770 850sam@headstrongtraining.com.auwww.headstrongtraining.com.au

```html
<!DOCTYPE html>
<html lang="en">
<head>
<meta charset="utf-8">
<title>Clear Path Coaching – Business Card</title>
<link href="https://fonts.googleapis.com/css2?family=Open+Sans:wght@300;400&display=swap" rel="stylesheet">
<style>
  :root {
    --page: #e9ebea;
    --card: #ffffff;
    --teal: #1bb5b4;
    --teal-deep: #0f9c9d;
    --teal-light: #6fd6d3;
    --logo-grey: #a39c9a;
    --ink: #222222;
    --muted: #4a4a4a;
  }
  html, body {
    margin: 0;
    width: 1200px;
    height: 902px;
    overflow: hidden;
    background: var(--page);
    font-family: "Open Sans", Arial, sans-serif;
  }
  .card {
    position: absolute;
    left: 150px;
    top: 194px;
    width: 900px;
    height: 514px;
    background: var(--card);
    box-shadow: 0 6px 24px rgba(0,0,0,0.18);
    overflow: hidden;
  }
  .card-shapes {
    position: absolute;
    inset: 0;
  }
  .brand {
    position: absolute;
    left: 70px;
    top: 60px;
  }
  .brand-mark {
    width: 140px;
    height: 140px;
    border-radius: 50%;
    border: 3px solid var(--teal-light);
    box-sizing: border-box;
    margin-left: 30px;
  }
  .brand-name {
    margin: 26px 0 0;
    font-weight: 300;
    color: var(--logo-grey);
    font-size: 40px;
    letter-spacing: 4px;
    line-height: 1.15;
    text-transform: uppercase;
  }
  .person {
    position: absolute;
    left: 70px;
    top: 372px;
  }
  .person-name {
    margin: 0;
    font-weight: 400;
    font-size: 36px;
    color: var(--teal);
    line-height: 1.1;
  }
  .person-role {
    margin: 4px 0 0;
    font-size: 20px;
    color: var(--muted);
  }
  .contact {
    position: absolute;
    right: 40px;
    top: 196px;
    margin: 0;
    padding: 0;
    list-style: none;
  }
  .contact-item {
    display: flex;
    justify-content: flex-end;
    align-items: center;
    gap: 14px;
    height: 32px;
    font-size: 19px;
    color: var(--ink);
  }
  .contact-icon {
    width: 20px;
    height: 20px;
    background: var(--ink);
    display: flex;
    align-items: center;
    justify-content: center;
  }
</style>
</head>
<body>
  <section class="card" aria-label="Business card">
    <svg class="card-shapes" viewBox="0 0 900 514" preserveAspectRatio="none" aria-hidden="true">
      <defs>
        <linearGradient id="swoosh" x1="0" y1="0" x2="1" y2="1">
          <stop offset="0" stop-color="#2cc3c0"/>
          <stop offset="1" stop-color="#0f9c9d"/>
        </linearGradient>
      </defs>
      <path d="M240 0 H900 V320 C820 170 600 70 240 0 Z" fill="url(#swoosh)"/>
      <path d="M240 0 C600 70 820 170 900 320 V300 C810 150 580 55 300 0 Z" fill="#7fdcd8" opacity="0.7"/>
      <path d="M0 514 V478 H500 L560 440 H620 L590 478 H900 V514 Z" fill="var(--teal)"/>
      <path d="M500 478 L560 440 H620 L590 478 Z" fill="var(--teal-deep)"/>
    </svg>

    <div class="brand">
      <div class="brand-mark"></div>
      <p class="brand-name">Clear Path<br>Coaching</p>
    </div>

    <div class="person">
      <p class="person-name">Rebecca Tanfield</p>
      <p class="person-role">Director</p>
    </div>

    <ul class="contact">
      <li class="contact-item">0491 362 517
        <span class="contact-icon"><svg width="12" height="12" viewBox="0 0 12 12"><path d="M2 1 L4 1 L5 4 L3.6 5 C4.4 6.8 5.4 7.8 7 8.4 L8 7 L11 8 V10 C11 10.6 10.6 11 10 11 C5 11 1 7 1 2 C1 1.4 1.4 1 2 1 Z" fill="#fff"/></svg></span>
      </li>
      <li class="contact-item">bec@clearpathcoaching.example.au
        <span class="contact-icon"><svg width="12" height="10" viewBox="0 0 12 10"><rect x="0.5" y="0.5" width="11" height="9" fill="none" stroke="#fff"/><path d="M0.5 0.5 L6 5.5 L11.5 0.5" fill="none" stroke="#fff"/></svg></span>
      </li>
      <li class="contact-item">www.clearpathcoaching.example.au
        <span class="contact-icon"><svg width="12" height="12" viewBox="0 0 12 12"><circle cx="6" cy="6" r="5" fill="none" stroke="#fff"/><path d="M1 6 H11 M6 1 C3.5 4 3.5 8 6 11 M6 1 C8.5 4 8.5 8 6 11" fill="none" stroke="#fff" stroke-width="0.8"/></svg></span>
      </li>
    </ul>
  </section>
</body>
</html>
```